Business Card for Industrial Distributor

We need a business card design for an industrial distributor. We sell machine parts for the manufacturing and oil industry. We would like the cards to look clean and modern but with a touch of industry.

Our colors are blue/white.

Please feel free to visit our website www.korvelpartsco.com

Target Market(s)

mexican manufacturers in the automobile/aerospace industry

Industry/Entity Type

Industrial

Colors
ffffff
0555a3

```html
<!DOCTYPE html>
<html lang="en">
<head>
<meta charset="utf-8">
<title>Korvel Business Card</title>
<link rel="stylesheet" href="https://fonts.googleapis.com/css2?family=Noto+Sans:wght@400;700;800&display=swap">
<style>
  :root {
    --brand-blue: #1f2b9c;
    --brand-blue-light: #2c41a8;
    --paper: #ffffff;
    --backdrop: #bdbdbd;
  }
  * { margin: 0; padding: 0; box-sizing: border-box; }
  html, body { width: 1200px; height: 800px; overflow: hidden; }
  body {
    background: var(--backdrop);
    font-family: "Noto Sans", Arial, sans-serif;
    position: relative;
  }
  .card {
    position: absolute;
    top: 245px;
    width: 540px;
    height: 309px;
    background: var(--paper);
    overflow: hidden;
    box-shadow: 0 6px 18px rgba(0,0,0,.18);
  }
  .card--back { left: 30px; background: linear-gradient(120deg, var(--brand-blue) 0%, var(--brand-blue-light) 100%); }
  .card--front { left: 630px; }

  /* back side */
  .back__name {
    position: absolute; left: 0; right: 0; top: 70px;
    text-align: center; color: var(--paper);
    font-weight: 800; font-size: 84px; letter-spacing: -1px;
  }
  .back__footer {
    position: absolute; left: 0; right: 0; bottom: 0; height: 62px;
    background: var(--paper);
    display: flex; align-items: center; justify-content: center;
    color: var(--brand-blue); font-size: 15px;
  }

  /* front side */
  .front__brand {
    position: absolute; top: 26px; right: 34px;
    display: flex; align-items: center; gap: 14px;
  }
  .brand__dot { width: 52px; height: 52px; border-radius: 50%; background: var(--brand-blue); }
  .brand__name { color: var(--brand-blue); font-weight: 800; font-size: 62px; letter-spacing: -1px; line-height: 1; }
  .front__band {
    position: absolute; left: 0; right: 0; top: 112px; height: 126px;
    background: var(--brand-blue);
    display: flex; align-items: center; padding: 0 34px;
    color: var(--paper);
  }
  .person { width: 220px; text-align: right; padding-right: 22px; }
  .person__name { font-weight: 700; font-size: 17px; letter-spacing: .5px; }
  .person__role { font-size: 14px; margin-top: -2px; }
  .divider { width: 1px; height: 84px; background: var(--paper); margin-right: 18px; }
  .contacts { list-style: none; font-size: 14px; line-height: 20px; }
  .contacts li { display: flex; align-items: center; gap: 8px; }
  .contacts svg { width: 14px; height: 14px; flex: none; }
  .front__address {
    position: absolute; left: 0; right: 0; bottom: 0; height: 71px;
    display: flex; align-items: center; padding-left: 60px;
    color: var(--brand-blue); font-size: 15px;
  }
</style>
</head>
<body>

<section class="card card--back">
  <div class="back__name">Korvel</div>
  <div class="back__footer">www.korvelpartsco.com</div>
</section>

<section class="card card--front">
  <div class="front__brand">
    <span class="brand__dot"></span>
    <span class="brand__name">Korvel</span>
  </div>

  <div class="front__band">
    <div class="person">
      <div class="person__name">DANIEL REYES</div>
      <div class="person__role">Manager</div>
    </div>
    <span class="divider"></span>
    <ul class="contacts">
      <li>
        <svg viewBox="0 0 14 14"><rect width="14" height="14" rx="2" fill="#fff"/><path d="M4 3h2l1 2.5-1.3 1a6 6 0 0 0 2.8 2.8l1-1.3L12 9v2a1 1 0 0 1-1 1A8 8 0 0 1 3 4a1 1 0 0 1 1-1z" fill="#1f2b9c"/></svg>
        (956) 555 - 0142
      </li>
      <li>
        <svg viewBox="0 0 14 14"><rect width="14" height="14" rx="2" fill="#fff"/><rect x="3" y="5" width="8" height="6" fill="#1f2b9c"/><rect x="4.5" y="2.5" width="5" height="3" fill="none" stroke="#1f2b9c"/></svg>
        (956) 555 - 0187
      </li>
      <li>
        <svg viewBox="0 0 14 14"><rect width="14" height="14" rx="2" fill="#fff"/><rect x="2.5" y="4" width="9" height="6.5" fill="none" stroke="#1f2b9c"/><path d="M2.5 4l4.5 4 4.5-4" fill="none" stroke="#1f2b9c"/></svg>
        sales@korvelpartsco.com
      </li>
      <li>
        <svg viewBox="0 0 14 14"><circle cx="7" cy="7" r="6.5" fill="#fff"/><circle cx="7" cy="7" r="4.5" fill="none" stroke="#1f2b9c"/><path d="M2.5 7h9M7 2.5v9" stroke="#1f2b9c"/></svg>
        www.korvelpartsco.com
      </li>
    </ul>
  </div>

  <div class="front__address">4120 Harbor Mill Rd. Brownsville, TX 78521</div>
</section>

</body>
</html>
```